Automotive Business Card Design

I would just like a automotive themed card. nothing too extravagant, but catchy.

needs to say something about doing roadside assistance,mobile repairs, Diesel repairs, and Fleet maintenance

it can be single sided or double sided. no preference there.

Industry/Entity Type

Automotive

Contact Information for Business Card

Dean Marlowe
phone 534 861 2093
Name: Brightpath Automotive & Diesel Repair

```html
<!DOCTYPE html>
<html lang="en">
<head>
<meta charset="utf-8">
<title>Brightpath Automotive &amp; Diesel Repair – Business Card</title>
<link rel="stylesheet" href="https://fonts.googleapis.com/css2?family=Libre+Baskerville:wght@400;700&display=swap">
<style>
  :root {
    --bg: #e9e6e1;
    --card-dark: #333333;
    --panel-grey: #e2e2e2;
    --paper: #ffffff;
    --accent: #e8401c;
    --photo-dark: #2b3038;
    --photo-mid: #6d6a6a;
    --photo-skin: #c98e6d;
  }
  * { box-sizing: border-box; margin: 0; padding: 0; }
  html, body {
    width: 1200px;
    height: 1037px;
    overflow: hidden;
    background: var(--bg);
    font-family: "Libre Baskerville", Georgia, serif;
  }
  .sheet {
    width: 1200px;
    height: 1037px;
    display: flex;
    flex-direction: column;
    align-items: center;
    justify-content: center;
    gap: 60px;
  }
  .card {
    width: 760px;
    height: 434px;
    background: var(--card-dark);
    padding: 32px;
    box-shadow: 0 3px 10px rgba(0,0,0,0.18);
  }

  /* Front side */
  .card-front__inner {
    display: flex;
    height: 100%;
    background: var(--paper);
  }
  .info-panel {
    width: 330px;
    display: flex;
    flex-direction: column;
    gap: 6px;
    background: var(--paper);
  }
  .info-panel__contact {
    background: var(--panel-grey);
    height: 82px;
    padding: 16px 20px 0 28px;
  }
  .contact-name {
    color: var(--accent);
    font-weight: 700;
    font-size: 25px;
    letter-spacing: 2px;
    line-height: 1.05;
  }
  .contact-phone {
    color: var(--accent);
    font-weight: 700;
    font-size: 16px;
    letter-spacing: 2px;
  }
  .info-panel__services {
    flex: 1;
    background: var(--panel-grey);
    padding: 26px 20px 0 28px;
    border-top: 3px solid var(--paper);
  }
  .services-title {
    color: var(--accent);
    font-weight: 700;
    font-size: 32px;
    letter-spacing: 0.5px;
    margin-bottom: 26px;
  }
  .services-list {
    list-style: none;
    color: var(--accent);
    font-weight: 700;
    font-size: 15px;
    line-height: 1.2;
  }
  .photo-frame {
    flex: 1;
    padding: 8px;
    background: var(--paper);
  }
  .photo-frame__border {
    width: 100%;
    height: 100%;
    border: 6px solid var(--accent);
  }
  .photo-frame__image {
    width: 100%;
    height: 100%;
    background: linear-gradient(150deg, var(--photo-mid) 0%, var(--photo-dark) 45%, var(--photo-skin) 100%);
  }

  /* Back side */
  .card-back__inner {
    height: 100%;
    background: var(--paper);
    padding: 7px;
  }
  .card-back__frame {
    height: 100%;
    border: 2px solid var(--accent);
    display: flex;
    align-items: center;
    justify-content: center;
  }
  .company-name {
    color: var(--accent);
    font-weight: 700;
    font-size: 23px;
    text-transform: uppercase;
    letter-spacing: 0.5px;
    text-align: center;
  }
</style>
</head>
<body>
<main class="sheet">
  <section class="card card-front">
    <div class="card-front__inner">
      <div class="info-panel">
        <div class="info-panel__contact">
          <p class="contact-name">Dean Marlowe</p>
          <p class="contact-phone">534 861 2093</p>
        </div>
        <div class="info-panel__services">
          <h2 class="services-title">SERVICES</h2>
          <ul class="services-list">
            <li>Roadside assistance</li>
            <li>Mobile repairs</li>
            <li>Diesel repairs</li>
            <li>And Fleet maintenance</li>
          </ul>
        </div>
      </div>
      <div class="photo-frame">
        <div class="photo-frame__border">
          <div class="photo-frame__image" role="img" aria-label="Photo of a mechanic's hands working on an engine with tools"></div>
        </div>
      </div>
    </div>
  </section>

  <section class="card card-back">
    <div class="card-back__inner">
      <div class="card-back__frame">
        <h1 class="company-name">Brightpath Automotive &amp; Diesel Repair</h1>
      </div>
    </div>
  </section>
</main>
</body>
</html>
```